Veldmark Supplies Business Card

Professional business card that stand out to our potential customers. Front and back with clean modern design

Industry/Entity Type

Oil and gas

Contact Information for Business Card

Name, address, website , office phone and cell number

Requirements
Must have
• Editable files for each employee

```html
<!DOCTYPE html>
<html lang="en">
<head>
<meta charset="utf-8">
<title>Veldmark Supplies – Business Card</title>
<link href="https://fonts.googleapis.com/css2?family=Open+Sans:wght@400;600;700;800&display=swap" rel="stylesheet">
<style>
  :root{
    --stage-dark:#0b0b0b;
    --stage-mid:#3a3a3a;
    --brand-cyan:#05b0d2;
    --brand-red:#ff0000;
    --ink-dark:#151515;
    --paper:#ffffff;
    --tint-pink:#fde0e3;
    --tint-blue:#dff2f8;
  }
  *{box-sizing:border-box;margin:0;padding:0}
  html,body{width:1200px;height:801px;overflow:hidden}
  body{
    background:radial-gradient(ellipse at 55% 50%,var(--stage-mid) 0%,var(--stage-dark) 75%);
    font-family:"Open Sans",Arial,sans-serif;
    position:relative;
  }
  .card{
    position:absolute;top:250px;width:525px;height:300px;border-radius:22px;overflow:hidden;
    box-shadow:0 14px 30px rgba(0,0,0,.55);
  }
  /* back side */
  .card--back{left:45px;background:var(--brand-cyan);display:flex;align-items:center;justify-content:center}
  .card--back .brand-name{color:var(--ink-dark);font-weight:800;font-size:30px;letter-spacing:.5px}
  /* front side */
  .card--front{left:630px;background:var(--paper)}
  .front-tint{
    position:absolute;left:0;top:0;width:60%;height:100%;
    background:linear-gradient(160deg,var(--tint-blue) 0%,var(--tint-pink) 55%,var(--paper) 100%);
  }
  .front-brand{
    position:absolute;left:28px;top:128px;display:flex;align-items:center;gap:9px;
  }
  .front-brand .mark{width:16px;height:16px;background:var(--brand-red)}
  .front-brand .brand-name{color:var(--brand-red);font-weight:800;font-size:23px}
  .red-panel{
    position:absolute;inset:0;background:var(--brand-red);
    clip-path:polygon(42% 0,100% 0,100% 100%,40% 100%,53% 50%);
  }
  .contact{position:absolute;left:285px;top:42px;color:var(--paper);width:225px}
  .contact .person{font-weight:800;font-size:24px;line-height:1;letter-spacing:.3px}
  .contact .role{font-size:12px;margin:4px 0 16px}
  .contact ul{list-style:none}
  .contact li{display:flex;align-items:flex-start;gap:8px;font-size:11px;line-height:1.35;margin-bottom:5px}
  .contact .icon{flex:0 0 14px;width:14px;height:14px;border-radius:50%;background:var(--paper);display:flex;align-items:center;justify-content:center;margin-top:1px}
  .contact .icon svg{width:9px;height:9px;fill:var(--brand-red)}
</style>
</head>
<body>
  <section class="card card--back" aria-label="Card back">
    <span class="brand-name">Veldmark Supplies</span>
  </section>

  <section class="card card--front" aria-label="Card front">
    <div class="front-tint" role="img" aria-label="Soft brand-colour backdrop"></div>
    <div class="front-brand">
      <span class="mark"></span>
      <span class="brand-name">Veldmark Supplies</span>
    </div>
    <div class="red-panel"></div>
    <div class="contact">
      <p class="person">DANIEL HARROW</p>
      <p class="role">Founder &amp; CEO</p>
      <ul>
        <li><span class="icon"><svg viewBox="0 0 10 10"><path d="M5 0a3.5 3.5 0 0 0-3.5 3.5C1.5 6 5 10 5 10s3.5-4 3.5-6.5A3.5 3.5 0 0 0 5 0zm0 5a1.5 1.5 0 1 1 0-3 1.5 1.5 0 0 1 0 3z"/></svg></span>423 Street Address Here, City<br>State &amp; Country, ZIP Code</li>
        <li><span class="icon"><svg viewBox="0 0 10 10"><path d="M2 0l2 2.5-1 1.2a6 6 0 0 0 3.3 3.3l1.2-1L10 8l-1.3 1.7C4 10 0 6 .3 1.3z"/></svg></span>(123) 456-7890</li>
        <li><span class="icon"><svg viewBox="0 0 10 10"><path d="M3 0h4a1 1 0 0 1 1 1v8a1 1 0 0 1-1 1H3a1 1 0 0 1-1-1V1a1 1 0 0 1 1-1zm0 1.5v6h4v-6z"/></svg></span>(123) 456-7890</li>
        <li><span class="icon"><svg viewBox="0 0 10 10"><path d="M2.5 0h5v3h-5zM0 3.5h10V8H8v2H2V8H0zm3 3v2.5h4V6.5z"/></svg></span>(123) 456-7890</li>
        <li><span class="icon"><svg viewBox="0 0 10 10"><path d="M0 2h10v6H0zm1 1v.3l4 2.5 4-2.5V3z"/></svg></span>info@yourwebsitehere.com</li>
        <li><span class="icon"><svg viewBox="0 0 10 10"><path d="M5 0a5 5 0 1 0 0 10A5 5 0 0 0 5 0zm0 1.2c.7.8 1.1 2.2 1.2 3.3H3.8C3.9 3.4 4.3 2 5 1.2zM3.8 5.5h2.4C6.1 6.6 5.7 8 5 8.8c-.7-.8-1.1-2.2-1.2-3.3z"/></svg></span>yourwebsitehere.com</li>
      </ul>
    </div>
  </section>
</body>
</html>
```